Business Card Design

We need a business card designed for our new company. Prefer a black card with white logo & writing.

Contact Information for Business Card

Ted Galloway, address: 7-4812 Fernhollow Road, Abbotsford, BC, V3K 8R2, Office Phone: 604-712-3390, Cell: 604-947-2164, Email: ted@resinworkshub.ca

Colors

Designer to choose only greyscale colors for use in the design.

```html
<!DOCTYPE html>
<html lang="en">
<head>
<meta charset="utf-8">
<title>Resin Works Hub – Business Card</title>
<link rel="stylesheet" href="https://fonts.googleapis.com/css2?family=Montserrat:wght@400;700;800&display=swap">
<style>
  :root {
    --canvas: #e9e9e9;
    --card: #232323;
    --ink: #ffffff;
    --ink-soft: #d9d9d9;
  }
  * { margin: 0; padding: 0; box-sizing: border-box; }
  html, body { width: 1200px; height: 1108px; overflow: hidden; }
  body {
    position: relative;
    background: var(--canvas);
    font-family: "Montserrat", Arial, sans-serif;
    color: var(--ink);
  }
  .card {
    position: absolute;
    width: 740px;
    height: 444px;
    background: var(--card);
  }
  .card--front { left: 241px; top: 68px; }
  .card--back  { left: 248px; top: 589px; }

  .brand {
    position: absolute;
    font-weight: 800;
    color: var(--ink);
    text-align: center;
    text-transform: uppercase;
    line-height: 1.05;
  }
  .card--front .brand {
    left: 482px; top: 84px; width: 230px;
    font-size: 30px; letter-spacing: 1px;
  }
  .card--back .brand {
    left: 0; right: 0; top: 176px;
    font-size: 64px; letter-spacing: 2px;
  }

  .holder { position: absolute; left: 37px; top: 206px; }
  .holder__name { font-size: 25px; font-weight: 700; letter-spacing: 0.2px; }
  .holder__role { margin-top: 6px; font-size: 15px; color: var(--ink-soft); }

  .divider {
    position: absolute;
    left: 37px; top: 271px;
    width: 643px; height: 2px;
    background: var(--ink);
  }

  .contact-list {
    position: absolute;
    left: 38px; top: 296px;
    list-style: none;
    font-size: 15.5px;
  }
  .contact-list li {
    display: flex; align-items: center;
    height: 26px;
    margin-bottom: 2px;
  }
  .contact-list li:nth-child(2) { margin-bottom: 0; }
  .contact-list svg { width: 16px; height: 16px; margin-right: 12px; flex: none; fill: var(--ink); }

  .address {
    position: absolute;
    right: 43px; top: 358px;
    text-align: right;
    font-size: 15.5px;
    line-height: 21px;
  }
</style>
</head>
<body>
  <section class="card card--front">
    <div class="brand">Resin Works<br>Hub</div>

    <div class="holder">
      <div class="holder__name">Ted Galloway</div>
      <div class="holder__role">owner</div>
    </div>
    <div class="divider"></div>

    <ul class="contact-list">
      <li>
        <svg viewBox="0 0 16 16" aria-hidden="true"><path d="M3.6 1.2l2.3 2.6-1.2 2a9 9 0 0 0 5.5 5.5l2-1.2 2.6 2.3-1.3 2.1C7.7 16 0 8.3.5 2.5z"/></svg>
        604-712-3390
      </li>
      <li>
        <svg viewBox="0 0 16 16" aria-hidden="true"><path d="M4.5 0h7a1 1 0 0 1 1 1v14a1 1 0 0 1-1 1h-7a1 1 0 0 1-1-1V1a1 1 0 0 1 1-1zm.5 2v10.5h6V2zm3 11.3a.9.9 0 1 0 0 1.8.9.9 0 0 0 0-1.8z"/></svg>
        604-947-2164
      </li>
      <li>
        <svg viewBox="0 0 16 16" aria-hidden="true"><path d="M1 4h14v1L8 9.2 1 5zm0 2.3l7 4.2 7-4.2V12H1z"/></svg>
        ted@resinworkshub.ca
      </li>
      <li>
        <svg viewBox="0 0 16 16" aria-hidden="true"><path d="M8 .5a7.5 7.5 0 1 0 0 15 7.5 7.5 0 0 0 0-15zM4 4.2l2 .8.6 1.8-1.4 1.3.4 2.2-1.4 1.4A5.8 5.8 0 0 1 4 4.2zm5.4 9.1l.4-2.2 1.6-1.3-.6-1.8-2-.4-.6-1.6 1.4-1.4a5.8 5.8 0 0 1-.2 8.7z"/></svg>
        www.resinworkshub.ca
      </li>
    </ul>

    <address class="address" style="font-style:normal">
      7-4812 Fernhollow Road,<br>
      Abbotsford, BC, V3K 8R2
    </address>
  </section>

  <section class="card card--back">
    <div class="brand">Resin Works<br>Hub</div>
  </section>
</body>
</html>
```